cryotherapy business . Whole Body Cryotherapy, Localised Cryotherapy, Cryofacials

Need home page plus services, about, pricing, online booking, contact and blog page

I want something slick, hip and professional. Our studio colours are duck egg blue, white and grey

I would also like a social media scroll at the bottom of every page

I will upload some web designs that I like the look of

Target Market(s)

Men and Women 25-45

Industry/Entity Type

Health And Wellness

Coding

Coded - Design and coding required

Number of Pages Required

5+ page

Font styles to use
Serif
Sans Serif

Requirements
Must have
• Must be eye catching and easy to navigate
Nice to have
• animation
Should not have
• Not sure what the site should not have. I am fairly open to ideas as this is a brand new business.

```html
<!DOCTYPE html>
<html lang="en">
<head>
<meta charset="utf-8">
<title>Frostvale — Cryotherapy Studio</title>
<link href="https://fonts.googleapis.com/css2?family=Montserrat:wght@400;500;600;700&family=Raleway:ital,wght@0,400;0,500;0,600;1,400&display=swap" rel="stylesheet">
<style>
:root{
  --duck:#a2c8d4;
  --duck-dark:#8fbccb;
  --ink:#222428;
  --text:#5a5d63;
  --grey-bg:#dcdde1;
  --white:#fff;
  --black:#0b0b0c;
  --about-tone-light:#eef0f3;
  --about-tone-mid:#c9ced6;
}
*{box-sizing:border-box;margin:0;padding:0}
html,body{width:1200px;height:5172px;overflow:hidden}
body{position:relative;font-family:"Raleway",sans-serif;color:var(--text);background:var(--white)}
.abs{position:absolute}
h2.section-title{position:absolute;left:0;width:1200px;text-align:center;font-family:"Montserrat",sans-serif;font-weight:600;font-size:36px;color:var(--ink);letter-spacing:.5px}
.btn{position:absolute;display:flex;align-items:center;justify-content:center;font-family:"Montserrat",sans-serif;font-weight:600;font-size:14px;border-radius:4px;text-transform:uppercase}
.btn-duck{background:var(--duck);color:#fff}
.btn-white{background:#fff;color:var(--duck)}
.btn-grey{background:#e2e3e5;color:var(--ink)}
.btn-dark{background:var(--black);color:#fff}

/* hero */
.hero{left:0;top:0;width:1200px;height:710px;background:linear-gradient(160deg,#7f8e98 0%,#a3aeb6 35%,#6b737b 65%,#3a3f45 100%)}
.logo{font-family:"Montserrat",sans-serif;font-weight:500;letter-spacing:4px;color:#fff}
.nav{position:absolute;top:30px;right:110px;display:flex;gap:32px;font-family:"Montserrat",sans-serif;font-weight:600;font-size:13px;color:#fff}
.hero-title{position:absolute;top:148px;left:0;width:1200px;text-align:center;font-family:"Montserrat",sans-serif;font-weight:500;font-size:50px;line-height:64px;color:#fff}
.dots{position:absolute;top:594px;left:575px;display:flex;gap:6px}
.dots span{width:12px;height:12px;border:2px solid #fff;border-radius:50%}
.dots span.on{background:var(--duck)}

/* about */
.about-image{left:112px;top:800px;width:456px;height:456px;border-radius:50%;background:radial-gradient(circle at 50% 50%,var(--about-tone-light) 0%,var(--about-tone-mid) 100%)}
.about-title{left:648px;top:822px;font-family:"Montserrat",sans-serif;font-weight:600;font-size:36px;color:var(--ink)}
.about-text{left:648px;top:898px;width:442px;font-size:15px;line-height:29px;text-align:justify}

/* benefits */
.benefits{left:0;top:1355px;width:1200px;height:780px;background:var(--grey-bg)}
.benefit{position:absolute;top:1545px;width:320px;height:470px;text-align:center}
.benefit.active{background:var(--duck)}
.benefit .ring{position:absolute;left:70px;top:26px;width:188px;height:188px;border-radius:50%;background:var(--duck)}
.benefit .disc{position:absolute;left:70px;top:36px;width:180px;height:180px;border-radius:50%;background:#343539;border:5px solid #fff}
.benefit h3{position:absolute;top:246px;width:100%;font-family:"Montserrat",sans-serif;font-weight:600;font-size:19px;color:var(--ink)}
.benefit.active h3{color:#fff}
.benefit p{position:absolute;top:280px;width:100%;font-size:15px;line-height:29px;color:#666}
.benefit.active p{color:#eef6f8}
.arrow{position:absolute;width:34px;height:34px;border-radius:50%;background:#111;display:flex;align-items:center;justify-content:center}

/* services */
.service{position:absolute;top:2320px;width:317px}
.service .pic{height:285px}
.service h4{margin-top:14px;font-family:"Montserrat",sans-serif;font-weight:600;font-size:18px;color:var(--ink)}
.service p{font-style:italic;font-size:15px;line-height:28px;color:#444;width:240px;margin-top:2px}
.service-dark{background:#26272a;color:#fff;font-size:14px;line-height:26px;text-align:center;padding:36px 30px 0}

/* pricing */
.pricing{left:0;top:2805px;width:1200px;height:685px;background:var(--grey-bg)}
.plan{position:absolute;top:3042px;width:236px;height:328px;background:#fff;border:2px solid #c9cbce;text-align:center}
.plan.featured{top:3023px;height:367px;background:var(--duck);border:none;color:#fff}
.plan h5{margin-top:38px;font-family:"Montserrat",sans-serif;font-weight:600;font-size:18px;color:var(--ink)}
.plan .price{font-family:"Montserrat",sans-serif;font-weight:600;font-size:42px;color:var(--ink);margin-top:4px}
.plan p{font-size:14px;line-height:29px;color:#444;padding:0 30px;margin-top:10px}
.plan.featured h5,.plan.featured .price,.plan.featured p{color:#fff}

/* booking */
.booking{left:0;top:3490px;width:1200px;height:380px;background:var(--duck);text-align:center;color:#fff}

/* contact */
.loc h6{font-family:"Montserrat",sans-serif;font-weight:600;font-size:19px;color:var(--ink)}
.loc .line{font-family:"Montserrat",sans-serif;font-weight:500;font-size:15px;color:#333;line-height:29px}
.map{position:absolute;left:562px;width:528px;height:278px;border:2px solid #d4d6da;background:linear-gradient(135deg,#e9ebee 0%,#dfe3e8 45%,#c8d6e6 60%,#e8eaed 100%)}

/* footer */
.footer{left:0;top:4760px;width:1200px;height:412px;background:var(--black);color:#fff}
.footer h6{font-family:"Montserrat",sans-serif;font-weight:600;font-size:19px;color:#fff}
.footer .links{font-size:15px;line-height:29px}
.field{position:absolute;left:800px;width:288px;height:44px;background:#fff;color:#888;font-size:14px;padding:12px 14px}
.social{position:absolute;top:5006px;width:64px;height:64px;border:2px solid #fff;border-radius:50%}
</style>
</head>
<body>

<!-- HERO -->
<section class="abs hero" role="img" aria-label="Woman relaxing in a whole body cryotherapy chamber with rising mist"></section>
<div class="abs logo" style="left:110px;top:22px;font-size:30px">FROSTVALE</div>
<nav class="nav"><span>HOME</span><span>SERVICES</span><span>ABOUT</span><span>PRICING</span><span>ONLINE BOOKING</span><span>CONTACT US</span></nav>
<h1 class="hero-title">ACCELERATE THE BODY’S NATURAL<br>HEALING PROCESS</h1>
<div class="dots"><span></span><span class="on"></span><span></span></div>
<svg class="abs" style="left:0;top:630px" width="1200" height="82" viewBox="0 0 1200 82">
  <path d="M0 18 C400 35 800 52 1200 62 L1200 82 L0 82Z" fill="#fff"/>
  <path d="M0 18 C400 35 800 52 1200 62 L1200 82 C800 70 400 58 0 50Z" fill="var(--duck)"/>
  <path d="M0 50 C400 58 800 70 1200 82 L0 82Z" fill="#fff"/>
</svg>

<!-- ABOUT -->
<div class="abs about-image" role="img" aria-label="Product photo of a whole body cryotherapy cabin"></div>
<h2 class="abs about-title">ABOUT US</h2>
<p class="abs about-text">Originally invented by doctors as a powerful anti-inflammatory tool, cryotherapy is a quick, noninvasive process that exposes your body to extreme cold of up to -250°F. This sudden drop in temperature increases circulation and pumps reoxygenated and nutrient enriched blood back into the bloodstream reducing pain &amp; inflammation and alleviating sore muscles. It’s also known to release ‘feel good’ endorphins that help improve sleep, reduce stress, and increase your metabolism.</p>
<div class="btn btn-duck" style="left:652px;top:1188px;width:143px;height:50px;font-size:13px">Read more ⊕</div>

<!-- BENEFITS -->
<section class="abs benefits" role="img" aria-label="Soft grey network pattern background"></section>
<h2 class="section-title" style="top:1450px">BENEFITS</h2>
<div class="arrow" style="left:38px;top:1753px"><svg width="16" height="16" viewBox="0 0 16 16"><path d="M10 2 L4 8 L10 14" stroke="#fff" stroke-width="3" fill="none"/></svg></div>
<div class="arrow" style="left:1124px;top:1753px"><svg width="16" height="16" viewBox="0 0 16 16"><path d="M6 2 L12 8 L6 14" stroke="#fff" stroke-width="3" fill="none"/></svg></div>

<div class="benefit" style="left:53px">
  <div class="ring"></div><div class="disc"></div>
  <svg class="abs" style="left:110px;top:90px" width="100" height="72" viewBox="0 0 100 72" fill="none" stroke="#fff" stroke-width="4"><rect x="14" y="14" width="12" height="44" rx="3"/><rect x="74" y="14" width="12" height="44" rx="3"/><rect x="4" y="24" width="10" height="24" rx="2"/><rect x="86" y="24" width="10" height="24" rx="2"/><line x1="26" y1="36" x2="74" y2="36"/></svg>
  <h3>SPORTS &amp; FITNESS</h3>
  <p>Reduce pain &amp; inflammation<br>Alleviate muscle soreness<br>Decrease recovery time</p>
  <div class="btn btn-duck" style="left:102px;top:380px;width:116px;height:40px;font-size:13px">Read more</div>
</div>
<div class="benefit active" style="left:428px">
  <div class="disc"></div>
  <svg class="abs" style="left:110px;top:82px" width="100" height="90" viewBox="0 0 100 90" fill="none" stroke="#fff" stroke-width="3.5"><path d="M40 6 q6 8 0 16 M50 6 q6 8 0 16"/><rect x="14" y="44" width="72" height="12"/><line x1="18" y1="56" x2="18" y2="76"/><line x1="82" y1="56" x2="82" y2="76"/><circle cx="74" cy="36" r="8"/><path d="M24 44 q20-14 42-6"/></svg>
  <h3>HEALTH &amp; WELLNESS</h3>
  <p>Increase metabolism<br>Replenish nutrients<br>Improve sleep</p>
  <div class="btn btn-white" style="left:102px;top:380px;width:116px;height:40px;font-size:13px">Read more</div>
</div>
<div class="benefit" style="left:808px">
  <div class="ring"></div><div class="disc"></div>
  <svg class="abs" style="left:118px;top:84px" width="84" height="84" viewBox="0 0 84 84" fill="none" stroke="#fff" stroke-width="3.5"><rect x="10" y="6" width="64" height="18"/><rect x="10" y="32" width="64" height="18"/><rect x="10" y="58" width="64" height="18"/><line x1="20" y1="15" x2="28" y2="15"/><line x1="20" y1="41" x2="28" y2="41"/><line x1="20" y1="67" x2="28" y2="67"/></svg>
  <h3>RELIEF &amp; RECOVERY</h3>
  <p>Improve immune system response<br>Decreased recovery time<br>Reduce pain &amp; inflammation</p>
  <div class="btn btn-duck" style="left:102px;top:380px;width:116px;height:40px;font-size:13px">Read more</div>
</div>

<!-- SERVICES -->
<h2 class="section-title" style="top:2235px">SERVICES</h2>
<div class="service" style="left:110px">
  <div class="pic" role="img" aria-label="Client standing in a whole body cryotherapy chamber" style="background:linear-gradient(180deg,#2a5fc9 0%,#9bb6e0 50%,#dfe6f0 100%)"></div>
  <h4>Whole Body Cryotherapy</h4><p>Relief &amp; rejuvenation for your entire body</p>
</div>
<div class="service" style="left:440px">
  <div class="pic service-dark">Local cryotherapy acts as a higher intensity, more efficient form of “icing.” With the use of liquid nitrogen, the treatment delivers colder, more consistent temperatures, more effectively targeting the problem
    <div style="margin-top:14px;font-family:Montserrat,sans-serif;font-weight:600;font-size:13px;color:var(--duck)">READ MORE ⊕</div></div>
  <h4>Local Cryotherapy</h4><p>Reduce pain, inflammation &amp; swelling in targeted areas</p>
</div>
<div class="service" style="left:770px">
  <div class="pic" role="img" aria-label="Client receiving a cryo facial treatment" style="background:linear-gradient(135deg,#c9cbcd 0%,#e9dcd3 50%,#f2f2f2 100%)"></div>
  <h4>Cryo Facial</h4><p>Slow down the aging process</p>
</div>

<!-- PRICING -->
<section class="abs pricing" role="img" aria-label="Soft grey network pattern background"></section>
<h2 class="section-title" style="top:2914px">PRICING</h2>
<div class="arrow" style="left:36px;top:3190px"><svg width="16" height="16" viewBox="0 0 16 16"><path d="M10 2 L4 8 L10 14" stroke="#fff" stroke-width="3" fill="none"/></svg></div>
<div class="arrow" style="left:1124px;top:3190px"><svg width="16" height="16" viewBox="0 0 16 16"><path d="M6 2 L12 8 L6 14" stroke="#fff" stroke-width="3" fill="none"/></svg></div>
<div class="plan" style="left:110px"><h5>SINGLE</h5><div class="price">$40</div><p>Lorem Ipsum is simply dummy text of the industry.</p><div class="btn btn-grey" style="left:50px;top:242px;width:128px;height:42px">Buy now</div></div>
<div class="plan featured" style="left:357px"><h5>10 PACK</h5><div class="price">$380</div><p>Lorem Ipsum is simply dummy text of the printing and typesetting industry.</p><div class="btn btn-dark" style="left:52px;top:287px;width:128px;height:42px">Buy now</div></div>
<div class="plan" style="left:604px"><h5>20 PACK</h5><div class="price">$720</div><p>Lorem Ipsum is simply dummy text of the industry.</p><div class="btn btn-grey" style="left:50px;top:242px;width:128px;height:42px">Buy now</div></div>
<div class="plan" style="left:851px"><h5>MONTHLY*</h5><div class="price">$400</div><p>Lorem Ipsum is simply dummy text of the industry.</p><div class="btn btn-grey" style="left:50px;top:242px;width:128px;height:42px">Buy now</div></div>

<!-- ONLINE BOOKING -->
<section class="abs booking">
  <h2 style="margin-top:70px;font-family:Montserrat,sans-serif;font-weight:500;font-size:36px">ONLINE BOOKING</h2>
  <p style="width:790px;margin:26px auto 0;font-size:14px;line-height:29px">It is a long established fact that a reader will be distracted by the readable content of a page when looking at its layout. The point of using Lorem Ipsum is that it has a more-or-less normal distribution of letters, as opposed to using ‘Content here, content here’, making it look like readable English.</p>
  <div class="btn" style="left:527px;top:265px;width:146px;height:48px;background:#fff;color:var(--ink);font-size:14px">Book now</div>
</section>

<!-- CONTACT -->
<h2 class="section-title" style="top:3968px">CONTACT US</h2>
<div class="abs loc" style="left:110px;top:4068px">
  <h6>HARBORVIEW</h6>
  <div class="line"><svg width="12" height="16" viewBox="0 0 12 16"><path d="M6 0a6 6 0 0 0-6 6c0 4.5 6 10 6 10s6-5.5 6-10A6 6 0 0 0 6 0z" fill="#333"/><circle cx="6" cy="6" r="2.2" fill="#fff"/></svg>&nbsp; 18 Quay Lane<br>&nbsp;&nbsp;&nbsp;&nbsp;&nbsp; 2nd Floor</div>
  <h6 style="margin-top:14px">HOURS</h6>
  <div class="line"><svg width="14" height="14" viewBox="0 0 14 14"><rect x="1" y="2" width="12" height="11" fill="none" stroke="#666" stroke-width="1.5"/><line x1="1" y1="5" x2="13" y2="5" stroke="#666" stroke-width="1.5"/></svg>&nbsp; Monday - Friday 6:30 am - 8:00 pm<br>&nbsp;&nbsp;&nbsp;&nbsp;&nbsp; Saturday 8:00 am - 1:00 pm<br>&nbsp;&nbsp;&nbsp;&nbsp;&nbsp; Sunday Closed</div>
  <div class="btn btn-duck" style="left:0;top:240px;width:212px;height:50px;font-size:19px;font-weight:500">Book a session</div>
</div>
<div class="abs loc" style="left:110px;top:4376px">
  <h6>ELMSTEAD</h6>
  <div class="line"><svg width="12" height="16" viewBox="0 0 12 16"><path d="M6 0a6 6 0 0 0-6 6c0 4.5 6 10 6 10s6-5.5 6-10A6 6 0 0 0 6 0z" fill="#333"/><circle cx="6" cy="6" r="2.2" fill="#fff"/></svg>&nbsp; 420 Mill Street<br>&nbsp;&nbsp;&nbsp;&nbsp;&nbsp; 3rd Floor</div>
  <h6 style="margin-top:14px">HOURS</h6>
  <div class="line"><svg width="14" height="14" viewBox="0 0 14 14"><rect x="1" y="2" width="12" height="11" fill="none" stroke="#666" stroke-width="1.5"/><line x1="1" y1="5" x2="13" y2="5" stroke="#666" stroke-width="1.5"/></svg>&nbsp; Monday - Friday 6:00 am - 7:00 pm<br>&nbsp;&nbsp;&nbsp;&nbsp;&nbsp; Saturday Closed<br>&nbsp;&nbsp;&nbsp;&nbsp;&nbsp; Sunday Closed</div>
  <div class="btn btn-duck" style="left:0;top:240px;width:212px;height:50px;font-size:19px;font-weight:500">Book a session</div>
</div>
<div class="map" style="top:4075px" role="img" aria-label="Street map showing the Harborview studio location"></div>
<div class="map" style="top:4375px;background:linear-gradient(120deg,#cfe6c4 0%,#e9ebee 25%,#eceef0 70%,#e2e5e9 100%)" role="img" aria-label="Street map showing the Elmstead studio location"></div>

<!-- FOOTER -->
<section class="abs footer">
  <svg class="abs" style="left:0;top:0" width="1200" height="50" viewBox="0 0 1200 50"><path d="M0 0 H1200 V30 C800 18 400 8 0 0Z" fill="#fff"/><path d="M0 0 C400 8 800 18 1200 30 V42 C800 26 400 12 0 6Z" fill="var(--duck)"/></svg>
  <div class="abs logo" style="left:110px;top:98px;font-size:34px;color:#e6e6e6">FROSTVALE</div>
  <p class="abs" style="left:110px;top:160px;width:290px;font-size:15px;line-height:29px">Lorem Ipsum is simply dummy text of the printing and typesetting industry.</p>
  <h6 class="abs" style="left:500px;top:112px">INFORMATION</h6>
  <div class="abs links" style="left:503px;top:160px">Home<br>services<br>about<br>pricing<br>online booking<br>contact us</div>
  <h6 class="abs" style="left:798px;top:112px">NEWSLETTER</h6>
  <div style="position:absolute;left:0;top:388px;width:1200px;text-align:center;font-size:14px">© Copyrights 2019 Frostvale | All Rights Reserved</div>
</section>
<div class="field" style="top:4920px">Your Name</div>
<div class="field" style="top:4975px">Email Address</div>
<div class="btn btn-duck" style="left:800px;top:5030px;width:124px;height:44px;font-size:14px">Subscribe</div>
<div class="social" style="left:109px" role="img" aria-label="Social profile link"></div>
<div class="social" style="left:186px" role="img" aria-label="Social profile link"></div>

</body>
</html>
```